Wordpress Design Project

We are a local restaurant who needs a quality online identity base. We operate in a 1930's Villa, and our target market is the below mid - upper. Our main sale is the evening dinner meal, while we also sell home-made goods, including preserves, and handmade chocolates.
The final Wordpress coded design will:
Be a base for information including Contact details, and a Map of it's location. It will also include photographs of some of the dishes to give an idea to potential customers as to the style and target market.
The site will have 4 main pages
-Main
-About
-Menu
-Contact
Ideas for elements we would like to have included in the design are
Cardboard tags with the links to the other pages, which give a home-made feel
Character wood, with deep grain to emphasis our homely feel
An 'aged' map of the location. Possibly on a large cardboard tag.
Link to our Facebook page
Link to our Plate Finder review page http://www.platefinder.co.nz/restaurant.php?rest=3927
Notes:
The final Wordpress site should communicate a homely inviting image, with deep character, while still looking elegant and slightly simplistic. We would like fine fonts, with nice spacing, especially on the cardboard tags.
I have attached a mockup of our very loose vision for the site to give you an idea of the line we would like to go down. This is just for initial ideas, and we are happy for radically different designs, or just neat variations on the base design
Professional, edited photos of the food available will be uploaded alongside this project
Villa Serena does not have an official Logo for use on the website, so a simple header that ties in with the page will be fine. This may be replaced eventually with a new logo
Address and Hosting is already setup with the address being www.villaserenakitchen.co.nz with a placeholder site online.
We look forward to all designs, and welcome any questions. This should be an nice job for someone with an eye for detail.

```html
<!DOCTYPE html>
<html lang="en">
<head>
<meta charset="utf-8">
<title>Villa Serena</title>
<link href="https://fonts.googleapis.com/css2?family=PT+Sans:wght@400;700&family=Arimo:wght@400;700&display=swap" rel="stylesheet">
<style>
:root{
  --forest:#1d3514;
  --forest-deep:#0f1f0b;
  --paper:#e6c98e;
  --paper-light:#efd7a3;
  --paper-edge:#c9a766;
  --tag:#ecd188;
  --ink:#2a2118;
  --body:#3b3024;
  --accent:#b0201a;
  --frame:#2b2b2b;
  --cream:#f1e6c8;
  --search:#d9aa55;
}
*{box-sizing:border-box;margin:0;padding:0}
html,body{width:740px;height:1200px;overflow:hidden}
body{position:relative;background:radial-gradient(ellipse at 50% 0%,#2f4e22 0%,var(--forest) 45%,var(--forest-deep) 100%);font-family:"Arimo",Arial,sans-serif;color:var(--body)}
.abs{position:absolute}
.nowrap{white-space:nowrap}

/* header */
.brand{left:38px;top:30px;font-family:"PT Sans",sans-serif;font-size:40px;color:#fff;font-weight:400;white-space:nowrap}
.contact-top{left:540px;top:16px;font-family:"PT Sans",sans-serif;color:#fff;white-space:nowrap}
.contact-top .phone{font-size:13px}
.contact-top .phone b{font-size:21px;font-weight:400}
.contact-top .mail{font-size:13px;margin-top:2px}
.search{left:503px;top:81px;width:210px;height:16px;display:flex}
.search .field{flex:1;background:#fff;font-size:8px;color:#999;padding:3px 5px;white-space:nowrap}
.search .btn{width:45px;background:var(--search);color:#fff;font-size:8px;text-align:center;line-height:16px}

/* paper */
.paper{left:20px;top:120px;width:700px;height:983px;background:radial-gradient(ellipse at 50% 40%,var(--paper-light) 0%,var(--paper) 60%,var(--paper-edge) 100%);box-shadow:0 0 8px rgba(0,0,0,.6)}

/* nav tags */
.nav{left:134px;top:120px;display:flex;gap:10px}
.nav a{display:block;width:138px;height:46px;background:var(--tag);clip-path:polygon(0 0,100% 0,100% 70%,50% 100%,0 70%);text-align:center;padding-top:7px;font-family:"PT Sans",sans-serif;font-size:17px;color:var(--ink);text-decoration:none;box-shadow:inset 0 0 0 1px #c9a35c;white-space:nowrap}

/* slider */
.slider{left:53px;top:182px;width:635px;height:252px;background:var(--frame);border-radius:4px 4px 40px 40px/4px 4px 14px 14px;box-shadow:0 3px 6px rgba(0,0,0,.5)}
.slide{left:63px;top:192px;width:613px;height:208px;background:radial-gradient(circle at 30% 30%,#f7c56a 0%,#a8652a 30%,#4a3122 65%,#25303a 100%)}
.arrow{top:263px;width:26px;height:51px;background:#2a2a2a}
.arrow.prev{left:28px;border-radius:26px 0 0 26px}
.arrow.next{left:688px;border-radius:0 26px 26px 0}
.dots{left:329px;top:415px;display:flex;gap:9px}
.dots span{width:11px;height:11px;border-radius:50%;background:#5a5a5a;box-shadow:inset 0 1px 2px #000}

/* welcome */
.welcome-title{left:246px;top:462px;font-size:13px;font-weight:400;color:var(--ink);border-bottom:1px dotted #8a7352;padding-bottom:4px;width:196px;white-space:nowrap}
.welcome-title em{font-style:normal;color:var(--accent)}
.login{left:46px;top:499px;width:164px;height:124px;border:1px solid #8d7650;border-radius:5px;background:var(--paper-light);box-shadow:0 2px 4px rgba(0,0,0,.35)}
.login h3{font-weight:400;font-size:12px;color:var(--ink);margin:10px 0 0 7px;padding:0 0 5px 29px;border-bottom:1px dotted #8a7352;width:150px}
.login label{position:absolute;font-size:8px;color:var(--ink);left:16px;white-space:nowrap}
.login .input{position:absolute;left:51px;width:101px;height:15px;background:#fff;border:1px solid #999}
.login .submit{position:absolute;left:54px;top:91px;width:63px;height:19px;border-radius:10px;background:linear-gradient(#444,#000);color:#fff;font-size:10px;font-weight:700;text-align:center;line-height:19px}
.welcome-photo{left:245px;top:499px;width:215px;height:127px;border:2px solid #fff;border-radius:4px;background:linear-gradient(135deg,#6f6a55,#b58d5e 45%,#3c3a2e)}
.welcome-text{left:472px;top:506px;width:232px;font-size:9px;line-height:17px}
.more{font-size:8px;color:var(--accent);white-space:nowrap}

/* boxes */
.box{border:1px solid #c9a766;border-radius:4px;background:rgba(239,215,163,.45)}
.box h2{position:absolute;font-weight:400;font-size:13px;color:var(--ink)}
.testimonials{left:35px;top:657px;width:669px;height:148px}
.testimonials h2{left:15px;top:10px}
.review{position:absolute;top:40px;width:330px;height:90px}
.review .face{position:absolute;left:15px;top:0;width:74px;height:56px;border:2px solid #fff;background:linear-gradient(#8a6a4c,#6e3b22)}
.review .click{position:absolute;left:15px;top:64px;width:68px;height:21px;border-radius:3px;background:linear-gradient(#333,#000);color:#fff;font-size:9px;text-align:center;line-height:21px;white-space:nowrap}
.review .date{position:absolute;left:104px;top:0;font-size:7px;white-space:nowrap}
.review p{position:absolute;left:104px;top:13px;width:215px;font-size:7px;line-height:14px}
.review .stars{position:absolute;left:104px;top:66px;display:flex;gap:1px}
.gallery{left:35px;top:820px;width:669px;height:218px}
.gallery h2{left:35px;top:13px}
.g-arrow{position:absolute;top:86px;width:11px;height:11px;border-radius:50%;background:#555}
.item{position:absolute;top:47px;width:130px}
.item .pic{width:124px;height:82px;border:1px solid #fff}
.item p{font-size:7px;line-height:13px;margin-top:6px}
.item .more{display:block;margin-top:6px}

/* footer */
.map{left:30px;top:1114px;width:81px;height:79px;background:linear-gradient(135deg,#e4e2dc,#c9c6bc)}
.foot-contact{left:129px;top:1114px;width:220px;height:84px;font-size:7px;color:var(--cream);line-height:12px}
.foot-contact > *{position:absolute;left:0;white-space:nowrap;font-weight:400;font-size:7px}
.social{left:586px;top:1115px;display:flex;gap:13px}
.social span{width:16px;height:16px;border-radius:2px}
.copy{right:27px;top:1146px;font-size:7px;color:var(--cream);white-space:nowrap}
</style>
</head>
<body>
<header>
  <div class="abs brand">Villa Serena</div>
  <div class="abs contact-top">
    <div class="phone">Phone: <b>03 415 0287</b></div>
    <div class="mail">Email: hello@villaserena.co.nz</div>
  </div>
  <div class="abs search"><div class="field">type your word here</div><div class="btn">SEARCH</div></div>
</header>

<main>
  <div class="abs paper"></div>
  <nav class="abs nav">
    <a href="#">About Us</a><a href="#">Menu</a><a href="#">Services</a><a href="#">Contact Us</a>
  </nav>

  <div class="abs slider"></div>
  <div class="abs slide" role="img" aria-label="Candle holders glowing on a dining table"></div>
  <div class="abs arrow prev"><svg width="26" height="51"><path d="M17 16 L10 25.5 L17 35" stroke="#fff" stroke-width="3" fill="none"/></svg></div>
  <div class="abs arrow next"><svg width="26" height="51"><path d="M9 16 L16 25.5 L9 35" stroke="#fff" stroke-width="3" fill="none"/></svg></div>
  <div class="abs dots"><span></span><span></span><span></span><span></span><span></span></div>

  <h1 class="abs welcome-title">WELCOME TO <em>VILLA SERENA</em></h1>

  <div class="abs login">
    <h3>Login</h3>
    <label style="top:45px">Name&nbsp; :</label><div class="input" style="top:42px"></div>
    <label style="top:72px">Email :</label><div class="input" style="top:68px"></div>
    <div class="submit">Submit</div>
  </div>

  <div class="abs welcome-photo" role="img" aria-label="Handmade chocolates in paper bags with tags"></div>
  <div class="abs welcome-text">
    <p>Nunc varius facilisis eros. Sed erat. In in velit quis arcu ornare laoreet. Curabitur adipiscing luctus massa.Integer ut purus ac augue commodo commodo. Nunc nec mi eu justo tempor consectetuer. Etiam vitae nisl. In dignissim lacus ut ante. Cras elit lectus, bibendum a, adipiscing vitae, commodo et, dui.</p>
    <p class="more" style="text-align:right;margin:9px 20px 0 0">View More &gt;&gt;</p>
  </div>

  <svg width="0" height="0" style="position:absolute"><defs><path id="st" d="M4.5 0 L5.6 3.3 L9 3.3 L6.3 5.3 L7.3 8.7 L4.5 6.6 L1.7 8.7 L2.7 5.3 L0 3.3 L3.4 3.3Z"/></defs></svg>

  <section class="abs box testimonials">
    <h2>Testimonials</h2>
    <div class="review" style="left:0">
      <div class="face" role="img" aria-label="Guest portrait"></div>
      <div class="click">Click Here</div>
      <div class="date">Jul 3, 2012</div>
      <p>Nunc varius facilisis eros. Sed erat. In in velit quis arcu ornare laoreet. Curabitur adipiscing luctus massa.Integer ut purus ac commodo Nunc varius facilisis eros.</p>
      <div class="stars"><svg width="50" height="9"><g fill="#8b1a1a"><use href="#st"/><use href="#st" x="10"/><use href="#st" x="20"/><use href="#st" x="30"/></g><use href="#st" x="40" fill="#333"/></svg></div>
    </div>
    <div class="review" style="left:346px">
      <div class="face" role="img" aria-label="Guest portrait"></div>
      <div class="click">Click Here</div>
      <div class="date">Jul 3, 2012</div>
      <p>Nunc varius facilisis eros. Sed erat. In in velit quis arcu ornare laoreet. Curabitur adipiscing luctus massa.Integer ut purus ac commodo Nunc varius facilisis eros.</p>
      <div class="stars"><svg width="50" height="9"><g fill="#8b1a1a"><use href="#st"/><use href="#st" x="10"/><use href="#st" x="20"/><use href="#st" x="30"/></g><use href="#st" x="40" fill="#333"/></svg></div>
    </div>
    <span class="abs more" style="right:14px;top:128px">View More &gt;&gt;</span>
  </section>

  <section class="abs box gallery">
    <h2>Gallery</h2>
    <div class="g-arrow" style="left:14px"></div>
    <div class="g-arrow" style="right:14px"></div>
    <div class="item" style="left:35px"><div class="pic" role="img" aria-label="Wine bottles and flowers" style="background:linear-gradient(135deg,#6a5a86,#7a4a2c 60%,#c9b48a)"></div><p>Nunc varius facilisis eros. Sed erat. In in velit quis arcu ornare laoreet. Curabitur adipiscing luctus massa.</p><span class="more">View More &gt;&gt;</span></div>
    <div class="item" style="left:189px"><div class="pic" role="img" aria-label="Plated meat dish" style="background:radial-gradient(circle,#6b3a1e 20%,#c98b4c 55%,#e9d7b5)"></div><p>Nunc varius facilisis eros. Sed erat. In in velit quis arcu ornare laoreet. Curabitur adipiscing luctus massa.</p><span class="more">View More &gt;&gt;</span></div>
    <div class="item" style="left:343px"><div class="pic" role="img" aria-label="Jar of home-made preserves" style="background:linear-gradient(135deg,#2a221c,#8a3a2c 50%,#2b2520)"></div><p>Nunc varius facilisis eros. Sed erat. In in velit quis arcu ornare laoreet. Curabitur adipiscing luctus massa.</p><span class="more">View More &gt;&gt;</span></div>
    <div class="item" style="left:499px"><div class="pic" role="img" aria-label="Plated roast dish" style="background:radial-gradient(circle,#b78532 20%,#6e4a22 55%,#3a2a1e)"></div><p>Nunc varius facilisis eros. Sed erat. In in velit quis arcu ornare laoreet. Curabitur adipiscing luctus massa.</p><span class="more">View More &gt;&gt;</span></div>
  </section>
</main>

<footer>
  <div class="abs map" role="img" aria-label="Street map of the restaurant location"></div>
  <div class="abs foot-contact">
    <h4 style="top:0">CONTACT</h4>
    <p style="top:18px">Nunc varius facilisis eros. Sed erat.</p>
    <p style="top:30px">In in velit quis arcu ornare laoreet.</p>
    <p style="top:48px">Phone: 03 415 0287</p>
    <p style="top:65px">Email: hello@villaserena.co.nz</p>
  </div>
  <div class="abs social">
    <span style="background:#3b5998"></span><span style="background:#3aa9d8"></span><span style="background:#e8612c"></span><span style="background:#1a7bb9"></span><span style="background:#5a9a3a"></span>
  </div>
  <div class="abs copy">© 2012 Villa Serena, All rights reserved</div>
</footer>
</body>
</html>
```